Create a memorable Stationary for Security Software Company

Velbrantix is the worldwide leader in securing the Internet. Making Internet communications and critical data secure, reliable and available everywhere has been and continues to be our ongoing vision. We are committed to staying focused on real customer needs and to developing new and innovative security solutions that redefine the security landscape.

Industry/Entity Type

Internet

Font styles to use
Serif
Sans Serif
Script

Colors
0792cd
33a6d7
85cae6

```html
<!DOCTYPE html>
<html lang="en">
<head>
<meta charset="utf-8">
<title>Velbrantix Business Card</title>
<link rel="stylesheet" href="https://fonts.googleapis.com/css2?family=Source+Sans+3:wght@400;600&display=swap">
<style>
  :root {
    --page-bg: #e6e2dc;
    --card-top: #5fb4de;
    --card-bottom: #3a90c6;
    --cloud-tone: #2a7fb6;
    --ink: #144f7c;
    --ink-soft: #1f5f8c;
    --brand: #0b5d92;
  }
  * { margin: 0; padding: 0; box-sizing: border-box; }
  html, body {
    width: 1200px; height: 969px; overflow: hidden;
    background: var(--page-bg);
    font-family: "Source Sans 3", Arial, sans-serif;
  }
  .card {
    position: absolute; left: 100px; top: 200px;
    width: 1000px; height: 570px;
    border-radius: 28px; overflow: hidden;
    background: linear-gradient(160deg, var(--card-top), var(--card-bottom));
    box-shadow: 0 10px 30px rgba(0,0,0,0.18);
  }
  .cloud-area {
    position: absolute; left: 0; right: 0; bottom: 0; height: 320px;
    background: linear-gradient(180deg, rgba(42,127,182,0) 0%, rgba(42,127,182,0.55) 35%, var(--cloud-tone) 100%);
  }
  .holder { position: absolute; left: 60px; top: 58px; color: var(--ink); }
  .holder-name { font-size: 36px; font-weight: 600; line-height: 1.1; }
  .holder-title { font-size: 27px; font-weight: 400; color: var(--ink-soft); margin-top: 2px; }
  .brand {
    position: absolute; left: 640px; top: 203px;
    display: flex; align-items: center; gap: 14px;
  }
  .brand-dot { width: 30px; height: 30px; border-radius: 50%; background: var(--brand); }
  .brand-name { font-size: 44px; font-weight: 600; color: var(--brand); line-height: 1; }
  .contact-list { position: absolute; left: 58px; top: 358px; list-style: none; color: var(--ink); }
  .contact-item { display: flex; align-items: center; gap: 16px; font-size: 26px; height: 39px; }
  .contact-icon { width: 22px; height: 22px; fill: var(--ink); flex: none; }
  .address {
    position: absolute; right: 64px; top: 442px;
    text-align right; font-size: 26px; line-height: 37px; color: var(--ink);
    text-align: right;
  }
</style>
</head>
<body>
  <div class="card">
    <div class="cloud-area" role="img" aria-label="Layered blue cloud illustration across the lower half of the card"></div>

    <div class="holder">
      <p class="holder-name">Marcus Hale</p>
      <p class="holder-title">CEO/Founder</p>
    </div>

    <div class="brand">
      <span class="brand-dot"></span>
      <span class="brand-name">Velbrantix</span>
    </div>

    <ul class="contact-list">
      <li class="contact-item">
        <svg class="contact-icon" viewBox="0 0 24 24"><path d="M6.6 10.8a15 15 0 0 0 6.6 6.6l2.2-2.2a1 1 0 0 1 1-.25 11.4 11.4 0 0 0 3.6.57 1 1 0 0 1 1 1V20a1 1 0 0 1-1 1A17 17 0 0 1 3 4a1 1 0 0 1 1-1h3.5a1 1 0 0 1 1 1c0 1.25.2 2.45.57 3.57a1 1 0 0 1-.25 1z"/></svg>
        614 502 7381
      </li>
      <li class="contact-item">
        <svg class="contact-icon" viewBox="0 0 24 24"><path d="M6 2h12v5H6zM3 8h18a1 1 0 0 1 1 1v8h-4v5H6v-5H2V9a1 1 0 0 1 1-1zm5 7v5h8v-5z"/></svg>
        614 502 7390
      </li>
      <li class="contact-item">
        <svg class="contact-icon" viewBox="0 0 24 24"><path d="M2 5h20v14H2zm2 2v.5l8 5 8-5V7z"/></svg>
        marcus@velbrantix.com
      </li>
      <li class="contact-item">
        <svg class="contact-icon" viewBox="0 0 24 24"><path d="M12 2a10 10 0 1 0 0 20 10 10 0 0 0 0-20zm0 2c1 0 2.3 2 2.8 5H9.2C9.7 6 11 4 12 4zm-3 7h6c0 .7 0 1.3-.1 2H9.1L9 11zm-4.9 0H7v2H4.1a8 8 0 0 1 0-2zm12.9 0h2.9a8 8 0 0 1 0 2H17v-2zM12 20c-1 0-2.3-2-2.8-5h5.6c-.5 3-1.8 5-2.8 5z"/></svg>
        www.velbrantix.com
      </li>
    </ul>

    <p class="address">2140 Harbor Crest Way<br>Port Elden, Oregon 97312</p>
  </div>
</body>
</html>
```